Concierge Healthcare Business Card Design and Logo

We need a logo and business card design for a new company called "Sound Haven". We will provide concierge audiological care, hearing aids, hearing exams, custom hearing protection etc to patients in the comfort of their homes and offices. We would like a sleek and modern design preferably with an Ear related logo.

Target Market(s)

People with hearing loss, Hunters, Musicians
My usual clientele are older individuals so usually 50+ years old

Industry/Entity Type

Health Care

Contact Information for Business Card

Celia Brandt, AuD
Audiologist
512-648-2917
soundhaven@mailvoro.com
www.soundhaven-vorel.com

Logo Text

Sound Haven

Number of Pages Required

3 page

```html
<!DOCTYPE html>
<html lang="en">
<head>
<meta charset="utf-8">
<title>Sound Haven — Business Card</title>
<link rel="stylesheet" href="https://fonts.googleapis.com/css2?family=Montserrat:wght@400;500;600&display=swap">
<style>
  :root {
    --backdrop: #2b2b2d;
    --card-dark: #000000;
    --card-light: #ffffff;
    --brand-blue: #29a9e1;
    --ink: #111111;
    --faint: #e4f3fb;
  }
  * { box-sizing: border-box; margin: 0; padding: 0; }
  html, body {
    width: 1200px; height: 900px; overflow: hidden;
    background: var(--backdrop);
    font-family: "Montserrat", Arial, sans-serif;
  }
  .canvas { position: relative; width: 1200px; height: 900px; }
  .card {
    position: absolute; left: 320px; width: 560px; height: 320px;
    border-radius: 18px; overflow: hidden;
    box-shadow: 0 12px 30px rgba(0,0,0,.45);
  }
  /* Back side */
  .card-back { top: 90px; background: var(--card-dark); color: var(--card-light); }
  .back-mark {
    position: absolute; left: 50%; top: 70px; transform: translateX(-50%);
    display: flex; align-items: center; gap: 14px;
  }
  .back-mark .dot {
    width: 26px; height: 26px; border-radius: 50%; background: var(--brand-blue);
  }
  .back-mark .name {
    font-weight: 500; font-size: 36px; letter-spacing: 6px; text-transform: uppercase;
    color: var(--card-light);
  }
  .back-url {
    position: absolute; left: 0; right: 0; top: 230px; text-align: center;
    font-size: 17px; font-weight: 400; letter-spacing: .5px;
  }
  /* Front side */
  .card-front { top: 480px; background: var(--card-light); color: var(--ink); }
  .front-decor { position: absolute; inset: 0; }
  .brand-lockup {
    position: absolute; left: 30px; top: 48px;
    display: flex; align-items: center; gap: 14px;
  }
  .brand-lockup .dot {
    width: 46px; height: 46px; border-radius: 50%; background: var(--brand-blue);
  }
  .brand-lockup .divider { width: 1px; height: 62px; background: var(--ink); }
  .brand-lockup .name {
    font-weight: 500; font-size: 24px; line-height: 1.15; letter-spacing: 5px;
    text-transform: uppercase; color: var(--ink);
  }
  .person { position: absolute; right: 26px; top: 60px; text-align: right; }
  .person-name { color: var(--brand-blue); font-weight: 600; font-size: 22px; }
  .person-title { font-size: 13px; font-weight: 400; margin-top: 2px; }
  .contact {
    position: absolute; left: 36px; top: 240px; list-style: none;
    font-size: 14px; line-height: 22px;
  }
  .contact li { display: flex; align-items: center; gap: 10px; }
  .contact svg { width: 11px; height: 11px; fill: var(--brand-blue); flex: none; }
</style>
</head>
<body>
<main class="canvas">
  <section class="card card-back" aria-label="Card back">
    <div class="back-mark">
      <span class="dot"></span>
      <span class="name">Sound Haven</span>
    </div>
    <p class="back-url">www.soundhaven-vorel.com</p>
  </section>

  <section class="card card-front" aria-label="Card front">
    <svg class="front-decor" viewBox="0 0 560 320" width="560" height="320" aria-hidden="true">
      <circle cx="220" cy="190" r="120" fill="none" stroke="var(--faint)" stroke-width="10"/>
      <line x1="300" y1="112" x2="540" y2="112" stroke="var(--brand-blue)" stroke-width="1.2"/>
      <line x1="20" y1="232" x2="378" y2="232" stroke="var(--brand-blue)" stroke-width="1.2"/>
      <polygon points="378,232 372,320 560,320 560,200 392,200" fill="#000"/>
      <polygon points="392,232 384,320 560,320 560,190 398,190" fill="var(--brand-blue)"/>
    </svg>

    <div class="brand-lockup">
      <span class="dot"></span>
      <span class="divider"></span>
      <span class="name">Sound<br>Haven</span>
    </div>

    <div class="person">
      <p class="person-name">Celia Brandt, AuD</p>
      <p class="person-title">Audiologist</p>
    </div>

    <ul class="contact">
      <li><svg viewBox="0 0 24 24"><path d="M6.6 10.8a15 15 0 0 0 6.6 6.6l2.2-2.2a1 1 0 0 1 1-.25 11.4 11.4 0 0 0 3.6.57 1 1 0 0 1 1 1V20a1 1 0 0 1-1 1A17 17 0 0 1 3 4a1 1 0 0 1 1-1h3.5a1 1 0 0 1 1 1c0 1.25.2 2.45.57 3.57a1 1 0 0 1-.25 1z"/></svg>512-648-2917</li>
      <li><svg viewBox="0 0 24 24"><path d="M2 5h20v14H2zm2 2v.5l8 5 8-5V7zm0 2.8V17h16V9.8l-8 5z"/></svg>soundhaven@mailvoro.com</li>
      <li><svg viewBox="0 0 24 24"><circle cx="12" cy="12" r="10"/></svg>www.soundhaven-vorel.com</li>
    </ul>
  </section>
</main>
</body>
</html>
```